Weightloss company needs Business Card

We want a business card that is clean and professional, yet portrays that we are a friendly, innovative, and versatile program designed to fit the needs of our clients.
I would like there to be 2 sides, one side having an appointment card, and the other side containing the logo and business information. There can be decorations on both sides. The logo is attached.

Target Market(s)

Men and women 40-60

Industry/Entity Type

Business

Contact Information for Business Card

Font styles to use
Sans Serif

Requirements
Must have
• The logo, space for business information
Nice to have
• The colors in the logo
Should not have
• No pictures of people or food

```html
<!DOCTYPE html>
<html lang="en">
<head>
<meta charset="utf-8">
<title>Turnpoint Wellness Business Card</title>
<link rel="stylesheet" href="https://fonts.googleapis.com/css2?family=Source+Sans+3:wght@400;600;700&display=swap">
<style>
  :root {
    --bg: #e9e6e1;
    --card: #ffffff;
    --red: #e8194a;
    --red-dark: #c8103b;
    --cyan: #3cc3e3;
    --ink: #3a3a3a;
    --muted: #6b6b6b;
    --dots: #8a8a8a;
  }
  * { margin: 0; padding: 0; box-sizing: border-box; }
  html, body { width: 1200px; height: 843px; overflow: hidden; }
  body {
    background: var(--bg);
    font-family: "Source Sans 3", Arial, sans-serif;
    position: relative;
  }
  .card {
    position: absolute;
    top: 267px;
    width: 540px;
    height: 309px;
    border-radius: 16px;
    background: var(--card);
    overflow: hidden;
    box-shadow: 0 6px 18px rgba(0,0,0,0.18);
  }
  .card--appointment { left: 40px; }
  .card--front { left: 620px; }

  /* Appointment side */
  .appt-title {
    position: absolute; top: 34px; left: 0; right: 0;
    text-align: center; color: var(--red);
    font-weight: 700; font-size: 24px;
  }
  .field {
    position: absolute; display: flex; align-items: flex-end;
    font-size: 16px; color: var(--ink);
  }
  .field .label { color: var(--red); font-weight: 600; margin-right: 6px; }
  .field .line {
    border-bottom: 2px dotted var(--dots);
    height: 1px; margin-bottom: 5px;
  }
  .field .suffix { margin-left: 8px; }
  .field .ampm { color: var(--red); font-size: 11px; font-weight: 600; margin-left: 4px; margin-bottom: 8px; }
  .field--name { top: 84px; left: 40px; }
  .field--name .line { width: 330px; }
  .field--time { top: 128px; left: 300px; }
  .field--time .line { width: 120px; }
  .field--blank { top: 140px; left: 40px; }
  .field--blank .line { width: 230px; }
  .field--date { top: 178px; left: 40px; }
  .field--date .line { width: 232px; }

  .days {
    position: absolute; top: 228px; left: 40px; right: 30px;
    display: flex; justify-content: space-between;
    list-style: none;
  }
  .day {
    display: flex; align-items: center; gap: 5px;
    color: var(--red); font-size: 15px; font-weight: 600;
  }
  .day .box {
    width: 16px; height: 12px; border: 1.5px solid var(--ink); border-radius: 2px;
  }
  .appt-note {
    position: absolute; bottom: 22px; left: 0; right: 0;
    text-align: center; font-size: 11px; color: var(--muted);
  }

  /* Front side */
  .card-art { position: absolute; inset: 0; }
  .person {
    position: absolute; top: 26px; left: 34px;
  }
  .person .name { color: var(--red); font-weight: 600; font-size: 20px; letter-spacing: 0.5px; }
  .person .role { color: var(--cyan); font-size: 14px; margin-top: -2px; }
  .brand {
    position: absolute; top: 104px; left: 34px;
    display: flex; align-items: center; gap: 10px;
  }
  .brand .mark {
    width: 22px; height: 22px; border-radius: 50%; background: var(--red);
  }
  .brand .wordmark {
    color: var(--red); font-weight: 700; font-size: 30px;
  }
  .contacts {
    position: absolute; top: 172px; right: 22px;
    list-style: none; text-align: right;
  }
  .contacts li {
    display: flex; justify-content: flex-end; align-items: center; gap: 10px;
    color: #fff; font-size: 16px; line-height: 23px;
  }
  .contacts svg { width: 14px; height: 14px; fill: #fff; }
  .address {
    position: absolute; bottom: 14px; right: 46px;
    color: #fff; font-size: 16px;
  }
</style>
</head>
<body>

<section class="card card--appointment" aria-label="Appointment side">
  <h2 class="appt-title">Next Appointment</h2>
  <div class="field field--name"><span class="line"></span><span class="suffix">has an appointment</span></div>
  <div class="field field--blank"><span class="line"></span></div>
  <div class="field field--time"><span class="label">Time :</span><span class="line"></span><span class="ampm">AM/PM</span></div>
  <div class="field field--date"><span class="label">Date :</span><span class="line"></span></div>
  <ul class="days">
    <li class="day">Sun <span class="box"></span></li>
    <li class="day">Mon <span class="box"></span></li>
    <li class="day">Tue <span class="box"></span></li>
    <li class="day">Wed <span class="box"></span></li>
    <li class="day">Thu <span class="box"></span></li>
    <li class="day">Fri <span class="box"></span></li>
    <li class="day">Sat <span class="box"></span></li>
  </ul>
  <p class="appt-note">Please give me 24 hours notice to cancel or change your appointment.</p>
</section>

<section class="card card--front" aria-label="Business information side">
  <svg class="card-art" viewBox="0 0 540 309" preserveAspectRatio="none" aria-hidden="true">
    <path d="M0,188 Q260,285 540,104 L540,122 Q260,300 0,202 Z" fill="var(--cyan)"/>
    <path d="M0,200 Q260,296 540,118 L540,309 L0,309 Z" fill="var(--red)"/>
    <path d="M0,240 Q260,300 540,170 L540,309 L0,309 Z" fill="var(--red-dark)" opacity="0.35"/>
  </svg>

  <div class="person">
    <p class="name">DANA WHITFIELD</p>
    <p class="role">CEO/FOUNDER</p>
  </div>

  <div class="brand">
    <span class="mark"></span>
    <span class="wordmark">Turnpoint Wellness</span>
  </div>

  <ul class="contacts">
    <li>555 214 7730
      <svg viewBox="0 0 24 24"><path d="M6.6 10.8a15 15 0 0 0 6.6 6.6l2.2-2.2a1 1 0 0 1 1-.25 11.4 11.4 0 0 0 3.6.57 1 1 0 0 1 1 1V20a1 1 0 0 1-1 1A17 17 0 0 1 3 4a1 1 0 0 1 1-1h3.5a1 1 0 0 1 1 1c0 1.25.2 2.45.57 3.6a1 1 0 0 1-.25 1z"/></svg>
    </li>
    <li>555 903 1186
      <svg viewBox="0 0 24 24"><path d="M7 1h10a2 2 0 0 1 2 2v18a2 2 0 0 1-2 2H7a2 2 0 0 1-2-2V3a2 2 0 0 1 2-2zm0 3v14h10V4zm5 15.5a1 1 0 1 0 0 2 1 1 0 0 0 0-2z"/></svg>
    </li>
    <li>hello@turnpointwell.com
      <svg viewBox="0 0 24 24"><path d="M2 5h20v14H2zm2 2v.4l8 5 8-5V7zm0 2.8V17h16V9.8l-8 5z"/></svg>
    </li>
    <li>www.turnpointwell.com
      <svg viewBox="0 0 24 24"><path d="M12 2a10 10 0 1 0 0 20 10 10 0 0 0 0-20zm-1 17.9A8 8 0 0 1 4.1 11H7c.1 3.3 1.6 6.4 4 8.9zM7 9H4.3A8 8 0 0 1 11 4.1C8.6 6.6 7.1 9 7 9zm6 10.9c2.4-2.5 3.9-5.6 4-8.9h2.9a8 8 0 0 1-6.9 8.9zM17 9c-.1 0-1.6-2.4-4-4.9A8 8 0 0 1 19.7 9z"/></svg>
    </li>
  </ul>
  <p class="address">412 Alder Court, Brookfield, Oregon 97321</p>
</section>

</body>
</html>
```